Now Leasing Banner

Looking for a banner that says the following information approx 4' x 30'

Now Leasing Maplebrook Terrace 925-318-6042

Target Market(s)

Drive by traffic

Industry/Entity Type

Residential property management

Requirements
Must have
• Clear and readable from a distance

```html
<!DOCTYPE html>
<html lang="en">
<head>
<meta charset="UTF-8">
<title>Now Leasing Banner – Maplebrook Terrace</title>
<link href="https://fonts.googleapis.com/css2?family=League+Gothic&display=swap" rel="stylesheet">
<style>
  :root {
    --page-bg: #e9ecf0;
    --banner-white: #ffffff;
    --brand-blue: #1f3fa8;
    --accent-grey: #b9bcc2;
    --light-grey: #dcdee2;
    --edge-shadow: rgba(0, 0, 0, 0.12);
  }
  html, body {
    margin: 0;
    padding: 0;
    width: 1200px;
    height: 800px;
    overflow: hidden;
    background: var(--page-bg);
  }
  .canvas {
    position: relative;
    width: 1200px;
    height: 800px;
    display: flex;
    align-items: center;
    justify-content: center;
  }
  .banner {
    position: relative;
    width: 1140px;
    height: 170px;
    background: var(--banner-white);
    box-shadow: 0 4px 14px var(--edge-shadow);
    display: flex;
    align-items: center;
    overflow: hidden;
  }
  .banner__end {
    flex: none;
    height: 100%;
  }
  .banner__end--left {
    width: 160px;
    background: linear-gradient(135deg, var(--brand-blue) 0%, var(--accent-grey) 55%, var(--light-grey) 100%);
    clip-path: polygon(0 0, 62% 0, 100% 50%, 62% 100%, 0 100%);
  }
  .banner__end--right {
    width: 50px;
    background: linear-gradient(225deg, var(--brand-blue) 0%, var(--accent-grey) 60%, var(--light-grey) 100%);
    clip-path: polygon(45% 0, 100% 0, 100% 100%, 45% 100%, 0 50%);
  }
  .banner__message {
    flex: 1;
    min-width: 0;
    margin: 0;
    padding: 0 16px;
    text-align: center;
    font-family: "League Gothic", "Arial Narrow", sans-serif;
    font-weight: 400;
    font-size: 60px;
    line-height: 1;
    letter-spacing: 0.5px;
    color: var(--brand-blue);
    text-transform: uppercase;
    white-space: nowrap;
  }
</style>
</head>
<body>
  <main class="canvas">
    <section class="banner" aria-label="Now leasing banner">
      <div class="banner__end banner__end--left" role="img" aria-label="Geometric chevron and diamond pattern in blue and grey"></div>
      <h1 class="banner__message">Now Leasing Maplebrook Terrace 925-318-6042</h1>
      <div class="banner__end banner__end--right" role="img" aria-label="Geometric chevron and diamond pattern in blue and grey"></div>
    </section>
  </main>
</body>
</html>
```